Halvik - consultancy website

I need a new design for my webpage/presence [to be functioning with Wordpress - I have a programmer to set it up but not the design idea].
My company is Halvik - a consultancy firm focused on growth management for Swedish SME's primarily;. We call it Leadership toolkit for firms on the rise, kind of a doctor helping small become big. Contentwise, its a simple frontpage + 3-4 subpages with content re company/myself/focus etc. The new site should communicate a fresh, trustworthy take yet simple and functional on all devices [i.e. think UI compatible for mobile/tablet]. Current building parts/form elements are
a) existing logo and text elements
b) existing pictures
c) the yellowish color
colours and new ideas on pictures/positioning are welcome. I prefer a 'full width page' solution with centralised text elements but that's all up to you to suggest. Current site is a quickfix made by myself - now I'm moving it to a new platform so want to take the opportunity to make it
Nothing superspecial as it is a 2-man show; on the other hand I still want to have a modern & fresh reflection of my brand in digital environments. Help me out!
www.halvik-demo.se
Best
Lina Bergqvist

```html
<!DOCTYPE html>
<html lang="en">
<head>
<meta charset="utf-8">
<title>Halvik – Leadership toolkit for firms on the rise</title>
<link href="https://fonts.googleapis.com/css2?family=Open+Sans:wght@300;400;600;700&family=Oswald:wght@400;500&display=swap" rel="stylesheet">
<style>
:root{
  --blue:#1d8fd8;
  --orange:#f39a12;
  --ink:#2b2b2b;
  --body:#7a7a7a;
  --rule:#e3e3e3;
  --footer:#232323;
  --footer-deep:#1a1a1a;
  --footer-text:#9a9a9a;
  --white:#ffffff;
}
*{box-sizing:border-box;margin:0;padding:0}
html,body{width:1200px;height:2416px;overflow:hidden}
body{font-family:"Open Sans",Arial,sans-serif;color:var(--body);background:var(--white);font-size:13px;line-height:1.6}
.wrap{width:1000px;margin:0 auto;position:relative}

/* header */
.site-header{height:88px;background:var(--white);border-bottom:1px solid var(--rule)}
.site-header .wrap{display:flex;align-items:center;justify-content:space-between;height:88px}
.brand{font-weight:700;font-size:34px;color:var(--ink);letter-spacing:-0.5px}
.main-nav{display:flex}
.main-nav a{display:block;padding:0 20px;line-height:85px;font-size:12px;font-weight:600;color:#555;text-decoration:none;border-top:3px solid transparent;border-left:1px solid var(--rule)}
.main-nav a:last-child{border-right:1px solid var(--rule)}
.main-nav a.is-active{border-top-color:var(--blue);color:var(--blue)}

/* hero */
.hero{position:relative;height:512px;overflow:hidden}
.hero-visual{position:absolute;inset:0;background:linear-gradient(180deg,#a3a7ab 0%,#80858a 50%,#3e4246 100%)}
.hero-copy{position:absolute;left:140px;top:372px;color:var(--white)}
.hero-title{font-family:"Oswald",sans-serif;font-weight:500;font-size:46px;line-height:1.1;text-transform:uppercase;letter-spacing:1px}
.hero-title span{display:block;font-size:34px;font-weight:400}
.hero-lead{margin-top:14px;font-size:13px;color:#e8e8e8;width:520px}
.hero-arrow{position:absolute;top:236px;width:34px;height:34px;background:rgba(0,0,0,.35)}
.hero-arrow.prev{left:0}.hero-arrow.next{right:0}

/* services */
.services{height:560px;padding-top:70px;text-align:center}
.section-title{font-weight:300;font-size:40px;color:var(--ink);letter-spacing:1px;text-transform:uppercase}
.rule{width:60px;height:2px;background:var(--blue);margin:10px auto 16px}
.services-intro{width:820px;margin:0 auto;font-size:13px}
.service-grid{display:grid;grid-template-columns:repeat(4,1fr);gap:40px;margin-top:56px}
.service-icon{width:70px;height:70px;border-radius:50%;background:var(--blue);margin:0 auto;display:flex;align-items:center;justify-content:center}
.service-name{margin-top:20px;font-size:13px;font-weight:600;color:var(--ink);text-transform:uppercase}
.service-text{margin-top:8px;font-size:12px;text-align:left;padding:0 10px}

/* about band */
.about{position:relative;height:380px;text-align:center;color:var(--white)}
.about-visual{position:absolute;inset:0;background:linear-gradient(180deg,#1a1c20 0%,#2b2e33 45%,#3a4048 75%,#1c1e22 100%)}
.about-inner{position:relative;padding-top:64px}
.about .section-title{color:var(--white)}
.about-text{width:920px;margin:0 auto;font-size:13px;color:#dcdcdc}
.btn-outline{display:inline-flex;align-items:center;gap:10px;margin-top:34px;border:2px solid var(--white);color:var(--white);padding:10px 26px;font-size:12px;font-weight:600;text-transform:uppercase;text-decoration:none}

/* who we are + blog */
.split{display:grid;grid-template-columns:430px 1fr;gap:150px;padding-top:40px;height:500px}
.col-title{font-size:22px;font-weight:400;color:var(--ink);text-transform:uppercase;padding-bottom:10px;border-bottom:1px solid var(--rule)}
.col-title.plain{text-transform:none}
.who-visual{margin-top:24px;height:150px;background:linear-gradient(120deg,#cfd5da 0%,#7f98a8 50%,#2f4656 100%)}
.who-name{margin-top:16px;font-size:15px;color:var(--ink)}
.who-text{margin-top:8px;font-size:12px}
.post{display:flex;gap:24px;margin-top:24px}
.post + .post{margin-top:22px}
.post-visual{flex:0 0 130px;height:100px;background:linear-gradient(135deg,#dfe6ee,#8ea4bb)}
.post-visual.alt{background:linear-gradient(135deg,#2a3440,#6b7d90)}
.post-title{font-size:14px;color:var(--ink)}
.post-date{font-size:11px;color:var(--blue);margin:2px 0 4px}
.post-text{font-size:12px}

/* feed band */
.feed{height:140px;background:var(--orange);color:var(--white)}
.feed .wrap{display:flex;align-items:center;gap:34px;height:140px}
.feed-mark{flex:0 0 64px;height:64px;border-radius:50%;background:var(--white);opacity:.95}
.feed-text{font-size:14px;line-height:1.7}
.feed-meta{font-size:12px;opacity:.85;margin-top:4px}

/* footer */
.site-footer{height:200px;background:var(--footer);color:var(--footer-text)}
.footer-grid{display:grid;grid-template-columns:1fr 1fr 1fr;gap:60px;padding-top:30px}
.footer-title{font-size:13px;color:var(--white);text-transform:uppercase;font-weight:600;margin-bottom:16px}
.contact-line{display:flex;gap:12px;align-items:flex-start;font-size:12px;margin-bottom:8px}
.contact-line svg{flex:0 0 16px;margin-top:2px}
.field{height:30px;background:#2e2e2e;border:1px solid #3a3a3a;margin-bottom:8px;font-size:11px;line-height:28px;padding:0 10px;color:#777}
.btn-subscribe{display:inline-block;background:#3a3a3a;color:var(--white);font-size:11px;padding:6px 20px;text-transform:uppercase}
.recent{font-size:12px;margin-bottom:10px;line-height:1.45}
.recent em{display:block;font-style:normal;color:var(--blue);font-size:11px}
.footer-bar{height:36px;background:var(--footer-deep);color:#777;font-size:11px}
.footer-bar .wrap{display:flex;justify-content:space-between;align-items:center;height:36px}
.social{display:flex;gap:8px;align-items:center}
.social-label{white-space:nowrap;margin-right:6px}
.social-dot{width:20px;height:20px;border-radius:50%;background:var(--blue);flex:0 0 20px}
</style>
</head>
<body>

<header class="site-header">
  <div class="wrap">
    <div class="brand">Halvik.</div>
    <nav class="main-nav">
      <a href="#" class="is-active">HOME</a>
      <a href="#">ABOUT US</a>
      <a href="#">WHAT W DO</a>
      <a href="#">WHO WE ARE</a>
      <a href="#">WHY W</a>
      <a href="#">CONTACT US</a>
    </nav>
  </div>
</header>

<section class="hero">
  <div class="hero-visual" role="img" aria-label="Businessman in a suit with a briefcase before a grey city skyline, a burst of colourful paint above his hand"></div>
  <div class="hero-arrow prev"></div>
  <div class="hero-arrow next"></div>
  <div class="hero-copy">
    <h1 class="hero-title">Leadership toolkit<span>for firms on the rise</span></h1>
    <p class="hero-lead">Lorem ipsum dolor sit amet, consectetur adipiscing elit, sed do eiusmod tempor incididunt ut labore et dolore magna aliqua.</p>
  </div>
</section>

<section class="services">
  <div class="wrap">
    <h2 class="section-title">What W Do</h2>
    <div class="rule"></div>
    <p class="services-intro">Consultancy services aiming to help high-performing organizations adapt to change and position themselves for sustainable growth. We bring structure, clarity and practical tools so that growing companies develop healthy, resilient leadership and scale with confidence.</p>
    <div class="service-grid">
      <div class="service">
        <div class="service-icon"><svg width="30" height="30" viewBox="0 0 30 30"><rect x="4" y="17" width="5" height="9" fill="#fff"/><rect x="12" y="11" width="5" height="15" fill="#fff"/><rect x="20" y="5" width="5" height="21" fill="#fff"/></svg></div>
        <div class="service-name">Growth Management</div>
        <p class="service-text">Lorem ipsum dolor sit amet, consectetur adipiscing elit, sed do eiusmod tempor incididunt ut.</p>
      </div>
      <div class="service">
        <div class="service-icon"><svg width="30" height="30" viewBox="0 0 30 30"><circle cx="15" cy="15" r="10" fill="none" stroke="#fff" stroke-width="2.5"/><path d="M5 15h20M15 5c-5 6-5 14 0 20M15 5c5 6 5 14 0 20" fill="none" stroke="#fff" stroke-width="2"/></svg></div>
        <div class="service-name">Corporate Communications</div>
        <p class="service-text">Lorem ipsum dolor sit amet, consectetur adipiscing elit, sed do eiusmod tempor incididunt ut.</p>
      </div>
      <div class="service">
        <div class="service-icon"><svg width="30" height="30" viewBox="0 0 30 30"><rect x="5" y="7" width="20" height="18" rx="2" fill="none" stroke="#fff" stroke-width="2.5"/><path d="M5 12h20M10 4v6M20 4v6" stroke="#fff" stroke-width="2.5"/></svg></div>
        <div class="service-name">Project Management</div>
        <p class="service-text">Lorem ipsum dolor sit amet, consectetur adipiscing elit, sed do eiusmod tempor incididunt ut.</p>
      </div>
      <div class="service">
        <div class="service-icon"><svg width="30" height="30" viewBox="0 0 30 30"><path d="M4 14h5v12H4zM11 14l5-9c2 0 3 1 3 3l-1 5h7c1.5 0 2 1 2 2l-2 9c0 1-1 2-2 2H11z" fill="#fff"/></svg></div>
        <div class="service-name">Conceptualizing</div>
        <p class="service-text">Lorem ipsum dolor sit amet, consectetur adipiscing elit, sed do eiusmod tempor incididunt ut.</p>
      </div>
    </div>
  </div>
</section>

<section class="about">
  <div class="about-visual" role="img" aria-label="Dark city skyline at dusk under heavy clouds"></div>
  <div class="about-inner">
    <h2 class="section-title">About Our Company</h2>
    <div class="rule"></div>
    <p class="about-text">Lorem ipsum dolor sit amet, consectetur adipiscing elit, sed do eiusmod tempor incididunt ut labore et dolore magna aliqua. Ut enim ad minim veniam, quis nostrud exercitation ullamco laboris nisi ut aliquip ex ea commodo consequat. Duis aute irure dolor in reprehenderit in voluptate velit esse cillum dolore eu fugiat nulla pariatur. Excepteur sint occaecat cupidatat non proident, sunt in culpa qui officia deserunt mollit anim id est laborum.</p>
    <a href="#" class="btn-outline">Read more
      <svg width="12" height="12" viewBox="0 0 12 12"><circle cx="6" cy="6" r="6" fill="#fff"/><path d="M5 3.5l2.5 2.5L5 8.5" fill="none" stroke="#222" stroke-width="1.5"/></svg>
    </a>
  </div>
</section>

<section class="wrap split">
  <div class="who">
    <h3 class="col-title">Who We Are</h3>
    <div class="who-visual" role="img" aria-label="Hand holding a magnifying glass over a glowing globe"></div>
    <div class="who-name">Nemo enim ipsam voluptatem</div>
    <p class="who-text">Lorem ipsum dolor sit amet, consectetur adipiscing elit, sed do eiusmod tempor incididunt ut labore et dolore magna aliqua. Ut enim ad minim veniam, quis nostrud exercitation ullamco laboris.</p>
  </div>
  <div class="blog">
    <h3 class="col-title plain">Latest Blog</h3>
    <article class="post">
      <div class="post-visual" role="img" aria-label="Person working on a laptop at a bright desk"></div>
      <div>
        <div class="post-title">Nemo Enim ipsam Voluptatem</div>
        <div class="post-date">JULY 19, 2015</div>
        <p class="post-text">Lorem ipsum dolor sit amet, consectetur adipiscing elit, sed do eiusmod tempor incididunt ut labore et dolore magna aliqua ut enim.</p>
      </div>
    </article>
    <article class="post">
      <div class="post-visual alt" role="img" aria-label="Businessman pointing at a glowing network diagram"></div>
      <div>
        <div class="post-title">Nemo Enim ipsam Voluptatem</div>
        <div class="post-date">JULY 16, 2015</div>
        <p class="post-text">Lorem ipsum dolor sit amet, consectetur adipiscing elit, sed do eiusmod tempor incididunt ut labore et dolore magna aliqua ut enim.</p>
      </div>
    </article>
  </div>
</section>

<section class="feed">
  <div class="wrap">
    <div class="feed-mark"></div>
    <div>
      <p class="feed-text">Lorem ipsum dolor sit amet, consectetur adipiscing elit, sed do eiusmod tempor incididunt ut labore et dolore magna aliqua. Ut enim ad minim veniam, quis nostrud exercitation ullamco.</p>
      <p class="feed-meta">2 hours ago · @halvik</p>
    </div>
  </div>
</section>

<footer class="site-footer">
  <div class="wrap footer-grid">
    <div>
      <h4 class="footer-title">Contact Us</h4>
      <div class="contact-line">
        <svg width="16" height="16" viewBox="0 0 16 16"><path d="M8 1a5 5 0 0 0-5 5c0 4 5 9 5 9s5-5 5-9a5 5 0 0 0-5-5z" fill="#9a9a9a"/><circle cx="8" cy="6" r="2" fill="#232323"/></svg>
        <span>Halvik<br>Storgatan 14, 411 38 Göteborg</span>
      </div>
      <div class="contact-line">
        <svg width="16" height="16" viewBox="0 0 16 16"><path d="M4 1l3 3-2 2c1 2 3 4 5 5l2-2 3 3-2 3C7 15 1 9 1 3z" fill="#9a9a9a"/></svg>
        <span>+46 31 700 12 34</span>
      </div>
      <div class="contact-line">
        <svg width="16" height="16" viewBox="0 0 16 16"><rect x="1" y="3" width="14" height="10" fill="#9a9a9a"/><path d="M1 3l7 6 7-6" fill="none" stroke="#232323" stroke-width="1.3"/></svg>
        <span>hej@halvik-demo.se</span>
      </div>
    </div>
    <div>
      <h4 class="footer-title">Sign up for newsletter</h4>
      <div class="field">Name</div>
      <div class="field">Email address</div>
      <span class="btn-subscribe">Subscribe</span>
    </div>
    <div>
      <h4 class="footer-title">Recent Posts</h4>
      <p class="recent">Lorem ipsum dolor sit amet, consectetur adipiscing elit sed do<em>Jul 19, 2015</em></p>
      <p class="recent">Lorem ipsum dolor sit amet, consectetur adipiscing elit sed do<em>Jul 16, 2015</em></p>
    </div>
  </div>
</footer>
<div class="footer-bar">
  <div class="wrap">
    <span>Halvik © 2015. All Rights Reserved.</span>
    <div class="social">
      <span class="social-label">Connect with us</span>
      <span class="social-dot"></span>
      <span class="social-dot"></span>
      <span class="social-dot"></span>
    </div>
  </div>
</div>

</body>
</html>
```